plumbers buisness card

A buisness card for a plumbing buisness
needs to have a water theme with navy blue, light blue and white
with an image of either a water drop, pipes, tools or something relating to plumbing and incorperating my buisness name as a logo

"Kettering Plumbing" is the words that need to stand out with "& gasfitting" to be smaller

spelling error on brief, "maintenance"
and also could you include my email d_kettering@mailwave.com.au

Industry/Entity Type

Plumbing

Contact Information for Business Card

Kettering Plumbing & Gasfitting

declan kettering
0432961085

specialising in
-new homes
-maitenance
-renovations

license no.
-73840

```html
<!DOCTYPE html>
<html lang="en">
<head>
<meta charset="utf-8">
<title>Kettering Plumbing &amp; Gasfitting – Business Card</title>
<link rel="stylesheet" href="https://fonts.googleapis.com/css2?family=Source+Sans+3:wght@400;700&display=swap">
<style>
  :root {
    --backdrop: #418f98;
    --card-white: #ffffff;
    --ink: #333132;
    --navy-rule: #2c4e86;
    --gold-strip: #b19f68;
    --photo-blue-deep: #1d4a9a;
    --photo-blue: #3a6fc0;
    --photo-silver: #d9dde2;
    --photo-steel: #8a8d90;
    --photo-dark: #2a2a2a;
  }
  * { margin: 0; padding: 0; box-sizing: border-box; }
  html, body {
    width: 1200px;
    height: 764px;
    overflow: hidden;
    background: var(--backdrop);
    font-family: "Source Sans 3", "Myriad Pro", Arial, sans-serif;
    color: var(--ink);
  }
  .business-card {
    position: absolute;
    left: 95px;
    top: 99px;
    width: 1007px;
    height: 575px;
    background: var(--card-white);
  }
  .card-info { position: absolute; left: 0; top: 0; width: 677px; height: 575px; }
  .brand-name {
    position: absolute; left: 47px; top: 68px;
    font-size: 54px; font-weight: 700; line-height: 1; letter-spacing: 0.2px;
  }
  .brand-sub {
    position: absolute; left: 47px; top: 148px;
    font-size: 42px; font-weight: 400; line-height: 1;
  }
  .contact-line {
    position: absolute; left: 47px; top: 251px;
    font-size: 31px; font-weight: 700; line-height: 1; white-space: nowrap;
  }
  .contact-line .phone { font-size: 25px; font-weight: 400; letter-spacing: 0.5px; }
  .services { position: absolute; left: 47px; top: 345px; font-size: 22px; line-height: 31px; }
  .services-title { font-weight: 700; }
  .services-list { padding-left: 5px; }
  .card-rule {
    position: absolute; left: 0; top: 466px; width: 677px; height: 3px;
    background: var(--navy-rule);
  }
  .license {
    position: absolute; left: 47px; top: 497px;
    font-size: 23px; font-weight: 700; line-height: 1;
  }
  .gold-strip {
    position: absolute; left: 677px; top: 0; width: 17px; height: 575px;
    background: var(--gold-strip);
  }
  .tap-photo {
    position: absolute; left: 694px; top: 0; width: 313px; height: 575px;
    background:
      linear-gradient(180deg, var(--photo-steel) 0%, rgba(138,141,144,0) 8%),
      linear-gradient(90deg, var(--photo-blue-deep) 0%, var(--photo-blue) 28%, var(--photo-silver) 48%, #b9bdc2 66%, var(--photo-steel) 82%, var(--photo-dark) 100%);
  }
</style>
</head>
<body>
  <section class="business-card">
    <div class="card-info">
      <h1 class="brand-name">Kettering Plumbing</h1>
      <p class="brand-sub">&amp; gasfitting</p>
      <p class="contact-line">Declan Kettering | <span class="phone">0432961085</span></p>
      <div class="services">
        <p class="services-title">Specialising in :</p>
        <p class="services-list">New homes - Maintenance - Renovations</p>
        <p class="email">email : d_kettering@mailwave.com.au</p>
      </div>
      <div class="card-rule"></div>
      <p class="license">license no. -73840</p>
    </div>
    <div class="gold-strip"></div>
    <div class="tap-photo" role="img" aria-label="Close-up photo of a chrome tap with a single water drop falling, against a blue background"></div>
  </section>
</body>
</html>
```